Maple Hollow Ranch Business Card

Farm selling Nigerian Dwarf Goats, Bison, chickens, and miniature donkeys. Additionally we sell goats milk, goats milk soap and goat cheese, bison meat, bison heads, and bison skins, and chicken eggs.
Address 4127 Tanager Lane
Hopkinsville, KY 42316
Phone number 615-392-5174
Website: MapleHollowRanch@quailmail.example
I will upload my farm logo, cheese label, and soap label to give you ideas of my theme.
I want a really catchy card that people will remember.

```html
<!DOCTYPE html>
<html lang="en">
<head>
<meta charset="utf-8">
<title>Maple Hollow Ranch Business Card</title>
<link rel="stylesheet" href="https://fonts.googleapis.com/css2?family=Exo+2:wght@400;500&family=Open+Sans:wght@400&display=swap">
<style>
  :root {
    --page-bg: #e9e6e1;
    --band-dark: #2f2621;
    --accent-gold: #e4a813;
    --panel-brown: #85511f;
    --panel-edge: #9c9891;
    --ink-dark: #3b2b1f;
    --ink-light: #ffffff;
    --logo-gold: #d9a42a;
  }
  * { box-sizing: border-box; margin: 0; padding: 0; }
  html, body { width: 1200px; height: 939px; overflow: hidden; }
  body { background: var(--page-bg); position: relative; }

  .card {
    position: absolute; left: 100px; top: 184px;
    width: 1000px; height: 572px;
    background: var(--accent-gold);
    overflow: hidden;
    box-shadow: 0 10px 30px rgba(0,0,0,.18);
  }
  .contact-panel {
    position: absolute; left: 80px; top: 250px;
    width: 875px; height: 265px;
    background: var(--panel-brown);
    border: 4px solid var(--panel-edge);
    display: flex;
  }
  .contact-item {
    flex: 1;
    border-right: 2px solid var(--panel-edge);
    display: flex; flex-direction: column; align-items: center;
    justify-content: flex-start;
    padding-top: 60px; gap: 26px;
    font-family: "Open Sans", sans-serif;
    font-size: 21px; line-height: 1.35; color: var(--ink-dark);
    text-align: center;
  }
  .contact-item:last-child { border-right: none; }
  .contact-icon { width: 34px; height: 34px; flex: none; }
  .contact-text { display: block; }

  .top-band {
    position: absolute; left: 0; top: 0;
    width: 1000px; height: 272px;
    background: var(--band-dark);
  }
  .person {
    position: absolute; left: 60px; top: 110px;
    font-family: "Exo 2", sans-serif; color: var(--ink-light);
  }
  .person-name { font-size: 46px; font-weight: 500; letter-spacing: 1px; }
  .person-role { font-size: 32px; font-weight: 500; margin-top: 6px; margin-left: 10px; }

  .brand {
    position: absolute; left: 470px; top: 40px;
    display: flex; align-items: center; gap: 24px;
  }
  .brand-mark {
    width: 150px; height: 150px; border-radius: 50%;
    border: 5px solid var(--logo-gold);
    flex: none;
  }
  .brand-name {
    font-family: "Exo 2", sans-serif; font-weight: 500;
    font-size: 31px; color: var(--logo-gold);
    letter-spacing: 1px; white-space: nowrap;
  }
</style>
</head>
<body>
  <div class="card">
    <div class="contact-panel">
      <div class="contact-item email">
        <svg class="contact-icon" viewBox="0 0 24 24" aria-hidden="true">
          <rect x="2" y="5" width="20" height="14" fill="var(--ink-dark)"/>
          <path d="M2 5 L12 13 L22 5" fill="none" stroke="var(--panel-brown)" stroke-width="1.6"/>
        </svg>
        <p class="contact-text">MapleHollowRanch<br>@quailmail.example</p>
      </div>
      <div class="contact-item phone">
        <svg class="contact-icon" viewBox="0 0 24 24" aria-hidden="true">
          <path d="M7 2 h3 l1.5 5 -2 1.5 c1 2.5 2.5 4.5 5 6 l1.5 -2 5 1.5 v3 c0 1.5 -1 2.5 -2.5 2.5 C10 19.5 4.5 14 4.5 4.5 4.5 3 5.5 2 7 2 z" fill="var(--ink-dark)"/>
        </svg>
        <p class="contact-text">615-392-5174</p>
      </div>
      <div class="contact-item address">
        <svg class="contact-icon" viewBox="0 0 24 24" aria-hidden="true">
          <path d="M12 2 C7.6 2 4.5 5.2 4.5 9.3 4.5 14.5 12 22 12 22 S19.5 14.5 19.5 9.3 C19.5 5.2 16.4 2 12 2 z" fill="var(--ink-dark)"/>
          <circle cx="12" cy="9.3" r="2.8" fill="var(--panel-brown)"/>
        </svg>
        <p class="contact-text">4127 Tanager Lane<br>Hopkinsville, KY 42316</p>
      </div>
    </div>

    <div class="top-band"></div>

    <div class="person">
      <p class="person-name">Johnathan Doe</p>
      <p class="person-role">Manager</p>
    </div>

    <div class="brand">
      <div class="brand-mark"></div>
      <p class="brand-name">Maple Hollow Ranch</p>
    </div>
  </div>
</body>
</html>
```